CODED website - Breakfree418

I am a successful entrepreneur - have recently sold my business and am semi-retired. I want to give something back, as well as provide a blog for articles and my journeys.

I will also be using this to provide free business and entrepreneurial advice.

I am creating a NOT FOR PROFIT business called Breakfree418.com.au which will provide the following;

1. Blog and articles; my travels, Small to Medium business advice and articles

2. My Bucket List - the 100 things I aim to achieve

3. Free business / start up advice - a section on the website which provides case studies on people / businesses which ask me for advice. We will then chronicle their story and what advice we have given for them to succeed.

My inspiration is the Martin Oxendale idea and website;

http://martinoxendale.example/about-martin/

Obviously I do NOT want a copy of this site, but use this for inspiration.

Furthermore, I would be interested in ongoing collaboration with the successful designer - I will be providing advice and consultancy to start ups, all of which will need web design etc, so there is ongoing referral streams for the successful designer.

I need this to be CODED and then uplifted to the website, so please DO NOT bid on this unless you can provide a coded site and facilitate the upload to BrightHosting.

The NECESSARY tabs / pages

Main landing page - a short introduction into the ethos of Breakfree418

Writing - this will be the blog articles

About

Our Bucket List - a section where we can add our 100 buket list items. Hyperlinked to open a new page which has details on each bucket list item (ie #1 Make Breakfree418 - hyperlink to a new page which then has info on the bucklist item and what we have done)

Breakfree418 - this will be the section where we discuss people / businesses that we are helping. We will have an opening intro section + a link to the contact us page so they can ask us for the free advice. This will be the section where we have case studies into businesses / people that we have helped.

Hey everyone!

I'm really keen to get this website launched and looking amazing - if you have any questions, or would like to discuss anything at all, please email me at

dane@pollwick.example.com.au

As I mentioned in the brief, I am doing this site to give back; I will not be earning a cent, and I will not be trying to earn any funds. I'm doing it simply to help other start ups or entrepreneurs, so I really want this site to look amazing.

I hope someone reads this and is inspired, and wants to be involved in this social enterprise with me.

Really excited to hear from you all and see your designs!

Industry/Entity Type

Business

Requirements
Must have
• MUST BE CODED and uplifted to the BrightHosting registered domain - www.breakfree418.com.au - happy to discuss additional costings for this with successful designer.

Separate pages for each section (as outlined in the brief above)

Blog section to look similar to http://martinoxendale.example/3x5/

Comprehensive website - not a simple wordpress template theme with some minor modifications. I will immediately reject any simple template design. I am looking for a slick, fully functioning website design.

PLEASE BE AWARE that I am looking for ongoing collaboration with the www.breakfree418.com.au.

I am trying this website as I want to find a young, energetic, vibrant, dynamic designer - this is your opportunity to be a part of something big, as this website will be huge!

Please do not submit a design if you are not motivated and ready for something big.

```html
<!DOCTYPE html>
<html lang="en">
<head>
<meta charset="utf-8">
<title>Breakfree418</title>
<link href="https://fonts.googleapis.com/css2?family=Arvo:wght@400;700&family=Noto+Serif&display=swap" rel="stylesheet">
<style>
:root{
  --outer:#231f17;
  --page:#d8cba7;
  --panel:#efe4c7;
  --rust:#b8531f;
  --rust-text:#b0522a;
  --ink:#3d362a;
  --muted:#5a5243;
  --rule:#c4b48c;
  --band:#ebdfbf;
  --badge:#7d6b48;
}
*{margin:0;padding:0;box-sizing:border-box}
html,body{width:847px;height:1200px;overflow:hidden;background:var(--outer);font-family:Arial,Helvetica,sans-serif;color:var(--ink)}
.page{position:absolute;left:86px;top:0;width:676px;height:1200px;background:var(--page)}
.abs{position:absolute}
.logo{left:162px;top:44px;width:195px;height:42px;background:#f7f2e6;display:flex;align-items:center;justify-content:center;font-family:Arvo,serif;font-weight:700;font-size:21px;color:var(--rust-text)}
.nav{left:121px;top:106px;width:608px;height:32px;background:var(--rust)}
.nav a{position:absolute;top:9px;color:#fff;font-family:Arvo,serif;font-size:9.5px;text-decoration:none}
.search{position:absolute;left:472px;top:10px;width:103px;height:14px;border-bottom:1px solid #d87a45;color:#fff;font-size:8px;padding:3px 4px}
.search svg{position:absolute;right:0;top:0}
.hero{left:134px;top:144px;width:580px;height:206px;background:radial-gradient(ellipse at 58% 85%,#ffe46a 0%,#f6a520 25%,#d8421a 60%,#8e1a0c 100%)}
.hero-ground{position:absolute;left:0;bottom:0;width:100%;height:22px;background:#1a0f08}
.quote{position:absolute;left:252px;top:78px;width:200px;font-family:"Noto Serif",serif;font-size:8.5px;line-height:12px;color:#3a1a0a}
.quote b{display:block;font-weight:400;font-size:11.5px;margin-top:3px}
.dots{position:absolute;left:531px;top:15px;display:flex;gap:3px}
.dots i{width:6px;height:6px;background:#6a5a50}
.dots i:first-child{background:#2a140a}
h2{font-family:Arvo,serif;font-weight:700;font-size:12px;color:var(--rust-text)}
.rule{height:1px;background:var(--rule)}
.photo{position:absolute}
.copy{font-size:7.4px;line-height:9.3px;color:var(--muted);text-align:justify}
.more{font-size:8px;color:var(--rust-text)}
.art-title{font-size:9.5px;color:var(--rust-text)}
.art-date{font-size:7.8px;color:var(--muted)}
.panel{background:var(--panel)}
.panel h2{padding:8px 7px 6px}
.bucket-item{position:absolute;left:14px;display:flex;gap:8px}
.badge{width:18px;height:18px;border-radius:50%;background:var(--badge);color:#fff;font-size:10px;font-weight:700;display:flex;align-items:center;justify-content:center;margin-top:5px;flex:none}
.bucket-item p{font-size:7px;line-height:9.3px;color:var(--muted)}
.bucket-item strong{color:var(--ink)}
.archive{position:absolute;left:8px;font-size:8.5px;color:var(--ink)}
.archive span{color:var(--muted);margin-right:14px}
.social{left:588px;width:84px;height:27px;background:var(--rust);border-radius:3px;color:#fff;font-family:Arvo,serif;font-weight:700;font-size:12px;display:flex;align-items:center;justify-content:center}
.footer-shade{left:134px;top:994px;width:580px;height:4px;background:linear-gradient(90deg,transparent,#c8b88e,transparent)}
.foot-text{font-size:8px;line-height:10.4px;color:var(--ink)}
.field{left:370px;top:1059px;width:149px;height:18px;background:#f6f1e4}
.submit{left:370px;top:1085px;width:52px;height:17px;background:var(--rust);color:#fff;font-size:8.5px;font-weight:700;display:flex;align-items:center;justify-content:center}
.bottom-band{left:0;top:1165px;width:847px;height:35px;background:var(--band)}
.bottom-links{left:134px;top:1179px;font-size:7.8px;color:var(--ink);word-spacing:2px}
.copyright{right:119px;top:1175px;font-size:7.8px;color:var(--ink)}
</style>
</head>
<body>
<div class="page"></div>

<div class="abs logo">Breakfree418</div>

<nav class="abs nav">
  <a style="left:41px">Home</a>
  <a style="left:98px">About us</a>
  <a style="left:168px">Articles</a>
  <a style="left:233px">Business Advises</a>
  <a style="left:339px">Travel Places</a>
  <a style="left:429px">Blog</a>
  <div class="search">Search
    <svg width="13" height="12" viewBox="0 0 13 12"><circle cx="5" cy="5" r="3.5" fill="none" stroke="#fff" stroke-width="1.6"/><line x1="7.6" y1="7.6" x2="11.5" y2="11" stroke="#fff" stroke-width="2"/></svg>
  </div>
</nav>

<section class="abs hero" role="img" aria-label="Savanna sunset with acacia tree, herder and elephant silhouettes">
  <div class="hero-ground"></div>
  <div class="quote">The world is a book and those who do not travel read only one page.”<b>Aurelio Venn</b></div>
  <div class="dots"><i></i><i></i><i></i><i></i></div>
</section>

<!-- About -->
<h2 class="abs" style="left:134px;top:363px">About My Travel</h2>
<div class="abs rule" style="left:134px;top:381px;width:410px"></div>
<div class="photo" role="img" aria-label="Traveller with suitcase on a desert plain" style="left:134px;top:398px;width:220px;height:132px;background:linear-gradient(180deg,#6e9ed6 0%,#a9c6e6 55%,#8a8f9a 62%,#e6e0d4 70%,#d8d0c0 100%)"></div>
<p class="abs copy" style="left:365px;top:399px;width:178px">At vero eos et accusamus et iusto odio dignissimos ducimus qui blanditiis praesentium voluptatum deleniti atque corrupti quos dolores et quas molestias excepturi sint occaecati cupiditate non provident, similique sunt in culpa qui officia deserunt mollitia animi, id est laborum et dolorum fuga. Et harum quidem rerum facilis est et expedita distinctio. Nam libero tempore, cum soluta nobis est eligendi optio cumque nihil impedit quo minus id quod maxime placeat facere possimus, omnis voluptas assumenda est, omnis dolor repellendus. Temporibus autem</p>
<a class="abs more" style="left:134px;top:539px">Read More ...</a>

<!-- Articles -->
<h2 class="abs" style="left:134px;top:567px">My Article’s</h2>
<div class="abs rule" style="left:134px;top:586px;width:410px"></div>

<div class="photo" role="img" aria-label="Airliner silhouette against an orange sunset" style="left:134px;top:609px;width:115px;height:93px;background:radial-gradient(circle at 40% 85%,#fff2c0 0%,#f0a040 25%,#d8701e 60%,#b55218 100%)"></div>
<div class="abs" style="left:262px;top:607px;width:282px">
  <div class="art-title">Climbing the St. Simons Lighthouse in Georgia</div>
  <div class="art-date">Friday, December 14, 2012</div>
  <p class="copy" style="margin-top:11px">After the muscular agony of climbing the 463 stairs of the Duomo in Florence I considered banning all future attractions with stairs, at least anything more than the ten it takes me to get to my bedroom. But, climbing to the top of a lighthouse was still on my bucket list. Unchecked. That is not acceptable</p>
  <div class="more" style="margin-top:10px">Read more ...</div>
</div>

<div class="photo" role="img" aria-label="Two hikers with backpacks looking over a misty valley" style="left:134px;top:735px;width:115px;height:93px;background:linear-gradient(160deg,#8fa6b8 0%,#c7d0d2 40%,#6a7a58 70%,#3c4a36 100%)"></div>
<div class="abs" style="left:262px;top:734px;width:282px">
  <div class="art-title">Climbing the St. Simons Lighthouse in Georgia</div>
  <div class="art-date">Friday, December 14, 2012</div>
  <p class="copy" style="margin-top:11px">After the muscular agony of climbing the 463 stairs of the Duomo in Florence I considered banning all future attractions with stairs, at least anything more than the ten it takes me to get to my bedroom. But, climbing to the top of a lighthouse was still on my bucket list. Unchecked. That is not acceptable</p>
  <div class="more" style="margin-top:10px">Read more ...</div>
</div>

<div class="photo" role="img" aria-label="Hammock under a palm tree on a tropical beach" style="left:134px;top:860px;width:115px;height:93px;background:linear-gradient(180deg,#2d86c8 0%,#8cc4e6 45%,#4fb3c0 62%,#efe8d6 75%,#e4dac4 90%,#1a1a1a 91%,#1a1a1a 100%)"></div>
<div class="abs" style="left:262px;top:860px;width:282px">
  <div class="art-title">Climbing the St. Simons Lighthouse in Georgia</div>
  <div class="art-date">Friday, December 14, 2012</div>
  <p class="copy" style="margin-top:11px">After the muscular agony of climbing the 463 stairs of the Duomo in Florence I considered banning all future attractions with stairs, at least anything more than the ten it takes me to get to my bedroom. But, climbing to the top of a lighthouse was still on my bucket list. Unchecked. That is not acceptable</p>
  <div class="more" style="margin-top:10px">Read more ...</div>
</div>

<!-- Sidebar -->
<aside class="abs panel" style="left:557px;top:358px;width:157px;height:192px">
  <h2>My Bucket List</h2>
  <div class="rule" style="width:157px"></div>
  <div class="bucket-item" style="top:37px"><span class="badge">1</span><p>67 Ideas for Your "Just Because" Bucket List<br>by <strong>ROSALIND</strong></p></div>
  <div class="bucket-item" style="top:75px"><span class="badge">2</span><p>56 Ideas For Your Fall<br>Bucket List<br>by <strong>ROSALIND</strong></p></div>
  <div class="bucket-item" style="top:112px"><span class="badge">3</span><p>60 Ideas for Your Spiritual<br>Bucket List<br>by <strong>ROSALIND</strong></p></div>
  <div class="bucket-item" style="top:149px"><span class="badge">4</span><p>Six Videos to Inspire Your<br>Bucket List<br>by <strong>ROSALIND</strong></p></div>
</aside>

<aside class="abs panel" style="left:557px;top:565px;width:157px;height:101px">
  <h2>My Archieves</h2>
  <div class="rule" style="width:157px"></div>
  <div class="archive" style="top:35px"><span>›</span>2012 (20)</div>
  <div class="archive" style="top:58px"><span>›</span>2011 (15)</div>
  <div class="archive" style="top:80px"><span>›</span>2020 (12)</div>
</aside>

<aside class="abs panel" style="left:557px;top:682px;width:157px;height:136px">
  <h2>My videos</h2>
  <div class="rule" style="width:157px"></div>
  <div class="photo" role="img" aria-label="Video still of two skiers on a snowy mountain" style="left:6px;top:30px;width:145px;height:94px;background:linear-gradient(180deg,#2c5aa8 0%,#6f94cc 45%,#e4ecf2 70%,#b9c6d2 92%,#1c1c1c 93%,#1c1c1c 100%)"></div>
</aside>

<h2 class="abs" style="left:564px;top:844px">Get Free Updates</h2>
<div class="abs rule" style="left:557px;top:863px;width:157px"></div>
<div class="abs social" style="top:870px">Friendbook</div>
<div class="abs social" style="top:906px">Chirper</div>
<div class="abs social" style="top:940px">ViewTube</div>

<!-- Footer -->
<div class="abs footer-shade"></div>

<h2 class="abs" style="left:135px;top:1007px">Testimonials</h2>
<svg class="abs" style="left:309px;top:1008px" width="8" height="13" viewBox="0 0 8 13"><path d="M1 5 L4 2 L7 5 M1 8 L4 11 L7 8" fill="none" stroke="#3d362a" stroke-width="1.2"/></svg>
<div class="abs rule" style="left:134px;top:1032px;width:192px"></div>
<div class="abs foot-text" style="left:135px;top:1042px;width:190px">
  <p>"Neque porro quisquam est qui dolorem ipsum quia dolor sit amet, consectetur, adipisci velit..."</p>
  <p style="margin-top:9px;font-size:7.5px">By ,Gordon Mitchell<br>Wednesday 19, Dec 2012</p>
  <p style="margin-top:11px">"Neque porro quisquam est qui dolorem ipsum quia dolor sit amet, consectetur, adipisci velit..."</p>
  <p style="margin-top:8px">By ,Gordon Mitchell<br>Wednesday 19, Dec 2012</p>
</div>

<h2 class="abs" style="left:369px;top:1007px">Newsletter</h2>
<div class="abs rule" style="left:369px;top:1032px;width:152px"></div>
<p class="abs foot-text" style="left:369px;top:1042px">Enter your e-mail ID to get free updates</p>
<div class="abs field"></div>
<div class="abs submit">SUBMIT</div>

<h2 class="abs" style="left:569px;top:1007px">Contact Us</h2>
<div class="abs rule" style="left:569px;top:1032px;width:145px"></div>
<div class="abs foot-text" style="left:569px;top:1040px">
  <p>Open Road HQ<br>2870 NE Larkspur Ave #214<br>Brookvale, OR 97388</p>
  <p style="margin-top:9px">Phone<br>+1.555.014.2290</p>
</div>

<div class="abs bottom-band"></div>
<div class="abs bottom-links">Help &nbsp; | &nbsp; Terms Privacy &nbsp; | &nbsp; Policy &nbsp; | &nbsp; Sitemap &nbsp; | &nbsp; Popular Products</div>
<div class="abs copyright">© Copyright 2012 breakfree418</div>
</body>
</html>
```